Business Card Design Can you design a business card design? Looking for something unique and differe

Can you design a business card design? Looking for something unique and different. Can you design a business card design? Looking for something unique and different.Can you design a business card design? Looking for something unique and different.Can you design a business card design? Looking for something unique and different.Can you design a business card design? Looking for something unique and different.Can you design a business card design? Looking for something unique and different.

Industry/Entity Type

Business

Contact Information for Business Card

Can you design a business card design? Looking for something unique and different.

Font styles to use
Serif

```html
<!DOCTYPE html>
<html lang="en">
<head>
<meta charset="utf-8">
<title>Solvane Cost Management – Business Card</title>
<link rel="stylesheet" href="https://fonts.googleapis.com/css2?family=Open+Sans:wght@400;600&display=swap">
<style>
  :root {
    --backdrop: #e4e4e4;
    --card: #0c0c0d;
    --card-edge: #1a1a1c;
    --lilac: #9c80b8;
    --stone: #8f8f8f;
    --ink-light: #f2f2f2;
    --rule: #6e6e6e;
  }
  * { box-sizing: border-box; margin: 0; padding: 0; }
  html, body {
    width: 1200px; height: 852px; overflow: hidden;
    background: var(--backdrop);
    font-family: "Open Sans", Arial, sans-serif;
  }
  .stage {
    width: 1200px; height: 852px;
    display: flex; align-items: center; justify-content: center; gap: 48px;
  }
  .card {
    position: relative;
    width: 520px; height: 300px;
    background: linear-gradient(135deg, var(--card-edge) 0%, var(--card) 55%);
    border-radius: 12px;
    overflow: hidden;
  }

  /* front */
  .brand {
    position: absolute; left: 0; right: 0; top: 96px;
    display: flex; flex-direction: column; align-items: center;
  }
  .brand-row { display: flex; align-items: center; gap: 14px; }
  .brand-mark { width: 26px; height: 26px; background: var(--stone); }
  .brand-name {
    color: var(--lilac); font-weight: 600; font-size: 52px; line-height: 1;
    letter-spacing: 0.5px;
  }
  .brand-tagline {
    margin-top: 12px; display: flex; align-items: center; gap: 10px;
    color: var(--stone); font-size: 11px; letter-spacing: 4px; text-transform: lowercase;
  }
  .brand-tagline::before, .brand-tagline::after {
    content: ""; width: 52px; height: 1px; background: var(--rule);
  }

  /* back */
  .back-brand {
    position: absolute; left: 34px; top: 130px;
    display: flex; align-items: center; gap: 12px;
  }
  .back-brand .brand-mark { width: 30px; height: 30px; }
  .back-brand .brand-name { font-size: 44px; }
  .holder { position: absolute; left: 300px; top: 44px; }
  .holder-name { color: var(--lilac); font-weight: 600; font-size: 17px; }
  .holder-role { color: var(--ink-light); font-size: 10px; margin-top: 3px; }
  .contacts {
    position: absolute; left: 300px; top: 132px;
    list-style: none; color: var(--ink-light); font-size: 12.5px; line-height: 1.6;
  }
  .contacts li { display: flex; align-items: center; gap: 9px; }
  .contacts svg { width: 12px; height: 12px; flex: none; fill: none; stroke: var(--ink-light); stroke-width: 1.4; }
  .address {
    position: absolute; left: 300px; top: 220px;
    color: var(--ink-light); font-size: 12.5px; line-height: 1.5;
  }
</style>
</head>
<body>
<main class="stage">
  <section class="card card-front">
    <div class="brand">
      <div class="brand-row">
        <span class="brand-mark"></span>
        <span class="brand-name">Solvane</span>
      </div>
      <div class="brand-tagline">cost management</div>
    </div>
  </section>

  <section class="card card-back">
    <div class="back-brand">
      <span class="brand-mark"></span>
      <span class="brand-name">Solvane</span>
    </div>
    <div class="holder">
      <p class="holder-name">Your Long Name</p>
      <p class="holder-role">Managing Director</p>
    </div>
    <ul class="contacts">
      <li>
        <svg viewBox="0 0 12 12"><path d="M2 1.5h2.5l1 2.5-1.5 1a6 6 0 0 0 3 3l1-1.5 2.5 1V10.5a1 1 0 0 1-1 1A9 9 0 0 1 .5 2.5a1 1 0 0 1 1.5-1z"/></svg>
        00.00.00.0000
      </li>
      <li>
        <svg viewBox="0 0 12 12"><rect x="1" y="2.5" width="10" height="7"/><path d="M1 2.5l5 4 5-4"/></svg>
        yourname@yourwebsite.com
      </li>
      <li>
        <svg viewBox="0 0 12 12"><circle cx="6" cy="6" r="5"/><path d="M1 6h10M6 1c-2.5 3-2.5 7 0 10M6 1c2.5 3 2.5 7 0 10"/></svg>
        www.yourwebsite.com
      </li>
    </ul>
    <p class="address">Your Commercial or office address<br>in just two line with pincode</p>
  </section>
</main>
</body>
</html>
```